WeatheredOnward.net wordpress design

Concept: Website where personal stories, personal videos can be posted as a challenge while awaiting the wisdom of experience from others who have WeatheredOnward same event or challenge in their lifetime.
Support aspects will be in 4 quadrants of Challenges:
1. Financial 2. Medical & Physical
3. Legal Matters 4. Psychological & Spiritual - ability to chat online with a spiritual/psychological counselor or life coach
Updates
Project Deadline Extended
Reason: Bit more time to complete designs.
Wanted to thank all of you for your designs! Greatly appreciated. Very creative ideas that captured the essence of this website. Will be back with a selection very shortly.
Target Market(s)
Anyone looking for a solution based upon experiential wisdom
Industry/Entity Type
Financial
Requirements
Must have
- Interactive website: Where you can post a challenge or issue via a written question or a video and ask for a solution.
Ability to access any of the 4 Quadrants (as listed above) to ask for an expert, via experience, advice and wisdom from those who have similar challenges.

```html
<!DOCTYPE html>
<html lang="en">
<head>
<meta charset="utf-8">
<title>WeatheredOnward.net</title>
<link href="https://fonts.googleapis.com/css2?family=Questrial&family=Mulish:wght@400;600;700;800&display=swap" rel="stylesheet">
<style>
:root{
  --page-bg:#efefef;
  --panel:#ffffff;
  --ink:#1d1d1d;
  --ink-soft:#4a4a4a;
  --muted:#8a8a8a;
  --line:#cfcfcf;
  --accent:#f7c23a;
  --accent-text:#d6901a;
  --bar:#1c1c1c;
  --pill:#8c8c8c;
}
*{box-sizing:border-box;margin:0;padding:0}
html,body{width:1063px;height:1200px;overflow:hidden}
body{background:var(--page-bg);font-family:"Questrial",sans-serif;color:var(--ink-soft);position:relative}
a{color:inherit;text-decoration:none}
.abs{position:absolute}

/* header */
.brand{left:126px;top:58px;display:flex;align-items:center;gap:10px}
.brand-mark{width:46px;height:46px;background:var(--accent);border-radius:4px}
.brand-name{font-family:"Mulish",sans-serif;font-weight:800;font-size:22px;color:var(--accent-text)}
.account{left:866px;top:48px;font-family:"Mulish",sans-serif;font-size:10px;font-weight:700;color:var(--ink)}
.account a{text-decoration:underline}
.account span{margin:0 14px}
.search{left:695px;top:74px;width:272px;height:26px;display:flex}
.search-field{flex:1;background:#fff;border:1px solid var(--line);border-radius:3px 0 0 3px}
.search-btn{width:80px;background:var(--accent);color:#fff;font-size:14px;display:flex;align-items:center;justify-content:center;border-radius:0 3px 3px 0}

/* page panel */
.panel{left:126px;top:136px;width:841px;height:1022px;background:var(--panel)}
.nav{left:126px;top:136px;width:841px;height:27px;background:var(--bar);border-radius:3px 3px 0 0;display:flex;color:#fff;font-size:14px}
.nav a{display:flex;align-items:center;padding-left:20px}
.nav .home{width:81px;background:var(--accent);font-weight:700;padding-left:18px}
.nav .n-profile{position:absolute;left:100px;padding:0;height:27px}
.nav .n-followers{position:absolute;left:183px;padding:0;height:27px}
.nav .n-uploads{position:absolute;left:290px;padding:0;height:27px}

/* hero */
.hero{left:134px;top:169px;width:583px;height:313px;background:linear-gradient(180deg,#8e959a 0%,#b8b9b4 45%,#9c8a6d 62%,#8a7152 80%,#9a8a78 100%)}
.hero-title{left:354px;top:413px;color:#fff;font-size:32px;line-height:1}
.hero-title b{font-family:"Mulish",sans-serif;font-weight:700}
.hero-sub{left:355px;top:448px;color:#fff;font-size:17px}

/* ask form */
.ask-title{left:736px;top:178px;font-size:19px;color:var(--ink-soft)}
.ask-desc{left:736px;top:207px;font-size:11.5px;line-height:14px;width:230px}
.field{position:absolute;left:735px;width:223px;height:23px;border:1px solid var(--line);border-radius:4px;font-size:11.5px;color:#a0a0a0;padding:4px 6px;background:#fff;box-shadow:inset 0 1px 2px rgba(0,0,0,.06)}
.btn-dark{position:absolute;background:var(--bar);color:#fff;font-family:"Mulish",sans-serif;font-weight:700;font-size:12px;display:flex;align-items:center;justify-content:center;border-radius:3px}
.panel-shadow{left:150px;top:486px;width:800px;height:14px;background:radial-gradient(ellipse at top,rgba(0,0,0,.08),transparent 70%)}

/* section titles */
.section-title{font-size:19px;color:var(--ink-soft)}
.rule{height:10px;background:radial-gradient(ellipse at top,rgba(0,0,0,.09),transparent 70%)}

/* articles */
.article{position:absolute;left:142px;width:380px}
.article h3{font-family:"Mulish",sans-serif;font-weight:700;font-size:13.5px;color:var(--ink);line-height:16px}
.article .meta{font-family:"Mulish",sans-serif;font-weight:700;font-size:9.5px;color:var(--accent-text);line-height:12px}
.share{display:flex;gap:2px;margin:4px 0 3px}
.share i{width:14px;height:14px;border-radius:2px;display:block}
.article p{font-size:11px;line-height:13px;width:365px}
.more{display:inline-block;background:var(--pill);color:#fff;font-size:10.5px;padding:0 7px;line-height:13px;border-radius:4px;margin-top:3px}

/* quadrants */
.quad{position:absolute;width:175px}
.quad h4{font-family:"Mulish",sans-serif;font-weight:700;font-size:15.5px;color:var(--ink);line-height:18px;margin-bottom:9px}
.quad .item{margin-bottom:7px;font-size:10.5px;line-height:12.5px;color:var(--muted)}
.quad .item b{font-family:"Mulish",sans-serif;font-weight:700;color:#6a6a6a;font-size:10.5px}
.quad .more{margin-top:0}

.chat-title{left:608px;top:1027px;font-size:19px;line-height:22px}
.chat-desc{left:608px;top:1079px;font-size:11.5px;line-height:14px}
</style>
</head>
<body>

<div class="abs brand"><span class="brand-mark"></span><span class="brand-name">WeatheredOnward</span></div>
<div class="abs account"><a href="#">Login</a><span>|</span><a href="#">Register</a></div>
<div class="abs search"><div class="search-field"></div><div class="search-btn">search</div></div>

<div class="abs panel"></div>
<nav class="abs nav">
  <a class="home" href="#">Home</a>
  <a class="n-profile" href="#">Profile</a>
  <a class="n-followers" href="#">Followers</a>
  <a class="n-uploads" href="#">My Uploads</a>
</nav>

<div class="abs hero" role="img" aria-label="Photo of a woman in a red dress with a scarf walking down a desert road toward distant mountains"></div>
<div class="abs hero-title">Learn from <b>Experience</b></div>
<div class="abs hero-sub">Experience is the best teacher overall</div>

<div class="abs ask-title">Ask your Question</div>
<div class="abs ask-desc">and get answered by the experienced people around the world</div>
<div class="field" style="top:251px">Name</div>
<div class="field" style="top:279px">email address</div>
<div class="field" style="top:306px;height:91px">your question</div>
<div class="field" style="top:401px">Select Quadrant</div>
<div class="field" style="top:429px;width:155px">Upload Video (optional)</div>
<div class="field" style="top:429px;left:894px;width:64px;text-align:center">Browse</div>
<div class="btn-dark" style="left:736px;top:457px;width:222px;height:23px">Get Answer</div>
<div class="abs panel-shadow"></div>

<div class="abs section-title" style="left:140px;top:528px">Fresh Articles</div>
<div class="abs section-title" style="left:610px;top:528px">Browse by Quadrant</div>
<div class="abs rule" style="left:150px;top:562px;width:780px"></div>

<div class="article" style="top:581px">
  <h3>Problem in life with Money</h3>
  <div class="meta">July 13, 2012<br>132 response, 8996 views</div>
  <div class="share"><i style="background:#f08a24"></i><i style="background:#f5a623"></i><i style="background:#3b5fa8"></i><i style="background:#c9d9e8"></i><i style="background:#45b0e5"></i><i style="background:#e8558f"></i></div>
  <p>This is Draftly's version of Lorem Ipsum. Proin gravida nibh vel velit auctor aliquet. Aenean sollicitudin, lorem quis bibendum auctor, nisi elit consequat ipsum, nec sagittis sem nibh id elit. Duis sed ...</p>
  <span class="more">more</span>
</div>
<div class="article" style="top:724px">
  <h3>Problem in life with Money</h3>
  <div class="meta">July 13, 2012<br>132 response, 8996 views</div>
  <div class="share"><i style="background:#f08a24"></i><i style="background:#f5a623"></i><i style="background:#3b5fa8"></i><i style="background:#c9d9e8"></i><i style="background:#45b0e5"></i><i style="background:#e8558f"></i></div>
  <p>This is Draftly's version of Lorem Ipsum. Proin gravida nibh vel velit auctor aliquet. Aenean sollicitudin, lorem quis bibendum auctor, nisi elit consequat ipsum, nec sagittis sem nibh id elit. Duis sed ...</p>
  <span class="more">more</span>
</div>
<div class="article" style="top:867px">
  <h3>Problem in life with Money</h3>
  <div class="meta">July 13, 2012<br>132 response, 8996 views</div>
  <div class="share"><i style="background:#f08a24"></i><i style="background:#f5a623"></i><i style="background:#3b5fa8"></i><i style="background:#c9d9e8"></i><i style="background:#45b0e5"></i><i style="background:#e8558f"></i></div>
  <p>This is Draftly's version of Lorem Ipsum. Proin gravida nibh vel velit auctor aliquet. Aenean sollicitudin, lorem quis bibendum auctor, nisi elit consequat ipsum, nec sagittis sem nibh id elit. Duis sed ...</p>
  <span class="more">more</span>
</div>
<div class="article" style="top:1010px">
  <h3>Problem in life with Money</h3>
  <div class="meta">July 13, 2012<br>132 response, 8996 views</div>
  <div class="share"><i style="background:#f08a24"></i><i style="background:#f5a623"></i><i style="background:#3b5fa8"></i><i style="background:#c9d9e8"></i><i style="background:#45b0e5"></i><i style="background:#e8558f"></i></div>
  <p>This is Draftly's version of Lorem Ipsum. Proin gravida nibh vel velit auctor aliquet. Aenean sollicitudin, lorem quis bibendum auctor, nisi elit consequat ipsum, nec sagittis sem nibh id elit. Duis sed ...</p>
  <span class="more">more</span>
</div>

<div class="quad" style="left:609px;top:586px">
  <h4>Financial Problems</h4>
  <div class="item"><b>Problem in life with Money</b><br>July 13, 2012<br>132 response, 8996 views</div>
  <div class="item"><b>Problem in life with Money</b><br>July 13, 2012<br>132 response, 8996 views</div>
  <div class="item"><b>Problem in life with Money</b><br>July 13, 2012<br>132 response, 8996 views</div>
  <span class="more">more</span>
</div>
<div class="quad" style="left:797px;top:586px">
  <h4>Legal Matters</h4>
  <div class="item"><b>Problem in life with Money</b><br>July 13, 2012<br>132 response, 8996 views</div>
  <div class="item"><b>Problem in life with Money</b><br>July 13, 2012<br>132 response, 8996 views</div>
  <div class="item"><b>Problem in life with Money</b><br>July 13, 2012<br>132 response, 8996 views</div>
  <span class="more">more</span>
</div>
<div class="quad" style="left:609px;top:806px">
  <h4>Medical &amp; Physical</h4>
  <div class="item"><b>Problem in life with Money</b><br>July 13, 2012<br>132 response, 8996 views</div>
  <div class="item"><b>Problem in life with Money</b><br>July 13, 2012<br>132 response, 8996 views</div>
  <div class="item"><b>Problem in life with Money</b><br>July 13, 2012<br>132 response, 8996 views</div>
  <span class="more">more</span>
</div>
<div class="quad" style="left:797px;top:806px">
  <h4>Psychological &amp;<br>Spiritual</h4>
  <div class="item"><b>Problem in life with Money</b><br>July 13, 2012<br>132 response, 8996 views</div>
  <div class="item"><b>Problem in life with Money</b><br>July 13, 2012<br>132 response, 8996 views</div>
  <span class="more">more</span>
</div>

<div class="abs rule" style="left:620px;top:1013px;width:320px"></div>
<div class="abs chat-title">Chat Online with a<br>Life Coach</div>
<div class="abs chat-desc">and get answered by the experienced<br>people around the world</div>
<div class="btn-dark" style="left:608px;top:1116px;width:221px;height:22px">Start Now</div>

</body>
</html>
```